The Harbourlight Dental centre, the Zorvik of dentistry

New concept of running a dental practice by having a walk in practice
WE ARE A HUSBAND AND WIFE TEAM

Really modern and sophisticated, we want it to feel different from the traditional dental practice.
we want it split into different pages:CONTACT US
LOCATION: Information about our location since patients often confuse us with the practice across the road
ABOUT US:
Opening hours - & 7 Days, We offer a weekend service
WALK IN: We offer a walk in service for dental treatments
TREATMENTS we offer

DENTAL ADVICE: Free dentist advise call back- So a dentist will call you back for free to discuss

Target Market(s)

Everyone

Industry/Entity Type

Dental

Coding

Coded - Design and coding required

Number of Pages Required

5+ page

Requirements
Must have
• First page
• * changing pictures
• *opening times
• * our walk in concept I.e. no appointment needed
• *logo
• * links in to clinic tidal (online booking system in Australia)
• * address /phone number/email
• * possible videos
• Second page
• meet the team
• third page
• dental treatments/walk in treatments
• fourth page
• dental advice with vid larko videos
• Fifth page
• contact us/maps/ we get confused with the dental practice across the road
• We would also like a giving back page. In this please include the photo's below of our dental mission in Guatemala, where by we did treatment for patients as part of a charity.
Nice to have
• Changing pictures on the home screen
• videos linked to home page

```html
<!DOCTYPE html>
<html lang="en">
<head>
<meta charset="utf-8">
<title>Meet the Team – The Harbourlight Dental centre</title>
<link rel="stylesheet" href="https://fonts.googleapis.com/css2?family=Open+Sans:wght@400;600;700&display=swap">
<style>
:root{
  --green:#9cc63b;
  --green-dark:#8ab52c;
  --blue:#1ea1dc;
  --text:#555;
  --muted:#777;
  --light:#f2f2f2;
  --form-bg:#e9e9e9;
  --dark:#3a3a3a;
  --darker:#333;
}
*{margin:0;padding:0;box-sizing:border-box}
html,body{width:733px;height:1200px;overflow:hidden;background:#fff}
body{font-family:"Open Sans",Arial,sans-serif;color:var(--text);position:relative}
.abs{position:absolute}
.topbar{top:0;left:0;width:733px;height:3px;background:linear-gradient(90deg,var(--green) 50%,var(--blue) 50%)}
.brand{left:81px;top:14px;display:flex;align-items:center;gap:8px}
.brand-square{width:30px;height:30px;background:var(--blue);border-radius:3px}
.brand-name{color:var(--green);font-weight:600;font-size:15px;line-height:16px;width:140px}
.info-top{right:82px;top:29px;font-size:6px;color:var(--muted);display:flex;gap:10px;align-items:center}
.info-top span,.contact-top span{display:flex;align-items:center;gap:3px}
.contact-top{right:82px;top:41px;font-size:10px;color:var(--blue);display:flex;gap:12px}
.nav{left:81px;top:77px;width:570px;height:32px;background:linear-gradient(#a8cf4a,var(--green-dark));display:flex}
.nav a{color:#fff;font-size:7.5px;text-decoration:none;display:flex;align-items:center;justify-content:center;height:100%;letter-spacing:.2px}
.nav a.active{background:var(--blue)}
.header-rule{top:110px;left:0;width:733px;height:4px;background:#eee}
.section-title{left:81px;top:129px;font-size:12px;color:#333}
.member{left:81px;width:570px}
.photo{position:absolute;left:0;top:0;width:148px;height:142px}
.bio{position:absolute;left:159px;top:0;width:411px}
.bio h2{font-weight:400;color:var(--green);font-size:20px;line-height:22px}
.bio .cred{color:var(--blue);font-size:10px;margin-top:2px}
.bio p{font-size:6.3px;line-height:11.7px;color:var(--muted);margin-top:6px}
.bio p + p{margin-top:11.7px}
.gallery{top:750px;left:0;width:733px;height:211px;background:var(--light)}
.gallery h3{position:absolute;top:17px;width:100%;text-align:center;font-weight:400;color:var(--green);font-size:20px}
.shot{position:absolute;top:52px;width:134px;height:112px}
.dots{position:absolute;top:180px;left:0;width:733px;display:flex;justify-content:center;gap:8px}
.dots i{width:6px;height:6px;border-radius:50%;background:#c8c8c8}
.dots i.on{background:var(--green)}
.map{top:961px;left:0;width:366px;height:151px;background:linear-gradient(135deg,#e4e4e4,#cfcfcf)}
.form-area{top:961px;left:366px;width:367px;height:151px;background:var(--form-bg)}
.form-area h3{position:absolute;left:31px;top:15px;font-weight:400;font-size:14px;color:#333}
.field{position:absolute;width:111px;height:22px;background:#fff;font-size:6.5px;color:#666;padding-left:10px;display:flex;align-items:center}
.submit{position:absolute;left:148px;top:101px;width:111px;height:22px;background:var(--dark);color:#fff;font-size:7px;display:flex;align-items:center;justify-content:center}
.footer{top:1112px;left:0;width:733px;height:88px;background:var(--dark);color:#ddd}
.f-row{position:absolute;top:14px;left:81px;width:570px;display:flex;align-items:center;font-size:6.5px}
.f-row span{display:flex;align-items:center;gap:5px}
.social{margin-left:auto;display:flex;gap:8px}
.social i{width:6px;height:6px;border-radius:50%;background:#888}
.f-rule{position:absolute;top:37px;left:81px;width:570px;height:1px;background:#555}
.f-links{position:absolute;top:50px;left:81px;font-size:5.5px;color:#ccc}
.copy{position:absolute;top:66px;left:81px;font-size:5.5px;color:#ccc}
.booking{position:absolute;top:55px;right:82px;display:flex;align-items:center;gap:10px;font-size:5.5px;color:#ccc}
.booking b{font-weight:400;font-size:12px;color:#bbb;display:flex;align-items:center;gap:5px}
.booking b i{width:9px;height:9px;background:#bbb}
</style>
</head>
<body>
<div class="abs topbar"></div>

<div class="abs brand">
  <div class="brand-square"></div>
  <div class="brand-name">The Harbourlight Dental centre</div>
</div>

<div class="abs info-top">
  <span><svg width="6" height="7" viewBox="0 0 10 12"><path d="M5 0a4 4 0 0 0-4 4c0 3 4 8 4 8s4-5 4-8a4 4 0 0 0-4-4zm0 5.5a1.5 1.5 0 1 1 0-3 1.5 1.5 0 0 1 0 3z" fill="#888"/></svg>Unit 4, 52 Fernway Boulevard, Wattlebrook, WA 6099.</span>
  <span><svg width="7" height="7" viewBox="0 0 10 10"><circle cx="5" cy="5" r="4" fill="none" stroke="#888" stroke-width="1.2"/><path d="M5 2.5V5h2" stroke="#888" fill="none"/></svg>OPEN 8 AM TO 8PM 7 DAYS A WEEK</span>
</div>
<div class="abs contact-top">
  <span><svg width="9" height="9" viewBox="0 0 10 10"><path d="M2 0l2 2.5-1 1.2c.6 1.3 1.7 2.4 3 3l1.2-1L10 8 8.5 10C4 9.5.5 6 0 1.5z" fill="#1ea1dc"/></svg>08 5550 2718</span>
  <span><svg width="10" height="8" viewBox="0 0 12 9"><rect width="12" height="9" fill="#1ea1dc"/><path d="M0 0l6 5 6-5" stroke="#fff" fill="none"/></svg>info@harbourlightdental.com</span>
</div>

<nav class="abs nav">
  <a href="#" style="width:67px">HOME</a>
  <a href="#" class="active" style="width:102px">MEET THE TEAM</a>
  <a href="#" style="width:208px">DENTAL TREATMENTS/WALK-IN TREATMENTS</a>
  <a href="#" style="width:95px">DENTAL ADVICE</a>
  <a href="#" style="width:98px">CONTACT US</a>
</nav>
<div class="abs header-rule"></div>

<div class="abs section-title">Principal dentists</div>

<section class="abs member" style="top:163px;height:150px">
  <div class="photo" role="img" aria-label="Portrait photo of Dr Priyan Kaleen" style="background:linear-gradient(135deg,#8a8a5a,#c9a58a 55%,#6b6040)"></div>
  <div class="bio">
    <h2>Dr Priyan Kaleen BDS</h2>
    <div class="cred">(Ashcombe, UK) MFDS RCS (Kelridge UK), DIP IMP (Surg)</div>
    <p>Dr Kaleen was the owner of a highly successful Private practice in London. He has extensive qualifications to continuously keep up to date with the latest dental developments to benefit his patients. He originally did his BDS at Ashcombe University UK. Dr Kaleen further completed his MFDSRCS Ed at Kelridge University.</p>
    <p>Dr Kaleen is also completing his MJDFRCS Eng at the Caldmoor College of Surgeons. He has gained extensive experience from the world renowned IMPLARA implant Institute in South America. He has worked in a mixture of Hospital specialty departments, Community Clinics, Government and Private practice. Dr Kaleen can connect well with anxious patients and enjoys improving patients confidence in relation to his teeth. He is currently undertaking a double MSc in fixed and removable prosthodontics in London.</p>
  </div>
</section>

<section class="abs member" style="top:342px;height:200px">
  <div class="photo" role="img" aria-label="Portrait photo of Dr Meera Sandell" style="background:linear-gradient(160deg,#efefef,#c9a48a 50%,#3d4a66)"></div>
  <div class="bio">
    <h2>Dr Meera Sandell BDS</h2>
    <div class="cred">(Thornfield, UK), BSC hons (Wexvale, UK), MJDF (Caldmoor College of Surgeons)</div>
    <p>Meera completed her BDS at Thornfield University UK, she then went on to complete her MJDF RCS Eng at the Caldmoor College of Surgeons. She also has a BSC Hons in Medical Biochemistry at Wexvale University UK.<br>Meera has worked in hospital where she was in the Oral and Maxillofacial surgery department and closely with the accident emergency department, dealing with cases deemed too difficult for general practice. She has also worked in private practice providing all forms of treatments, where she particularly enjoys helping anxious patients overcome their barrier of visiting the Dentist.</p>
    <p>Meera and Priyan are highly ethical individuals who believe in an open and honest relationship with their patients. They strongly believe patients matter and want them to leave with a smile.</p>
    <p>Charity work is close to both dentists heart. They recently went to Guatemala to undertake a dental mission with a team of international dentists to provide dental treatment for poverty stricken families. (SEE PICTURES IN FILE OF CHARITY WORK)</p>
    <p>Also in 2011 Meera went out to Peru and provided dental treatment to poverty stricken families and promoted oral health.</p>
  </div>
</section>

<section class="abs member" style="top:574px;height:150px">
  <div class="photo" role="img" aria-label="Portrait photo of practice manager Elise Marrow" style="background:linear-gradient(150deg,#b8b0a8,#c79a80 50%,#5a4a40)"></div>
  <div class="bio">
    <h2>Elise Marrow</h2>
    <div class="cred">Manager</div>
    <p>Aliquam erat volutpat. Quisque aliquet ex nec est vestibulum pulvinar. Pellentesque convallis molestie enim sit amet efficitur. Etiam id imperdiet lectus. Vivamus lacus justo, ultrices nec erat in, euismod iaculis mauris. Vivamus eleifend vitae nulla vel malesuada. In ac malesuada lacus, et consectetur ante. Fusce vitae lectus sit amet mi pulvinar maximus. Aenean placerat, nibh vel accumsan aliquet, magna nibh accumsan nibh, ac tempus nunc ipsum ac tellus. Cras augue magna, placerat eget nulla non, congue suscipit neque.</p>
    <p>Proin a dolor mauris. Vestibulum ante ipsum primis in faucibus orci luctus et ultrices posuere cubilia Curae; Vestibulum eget nisl metus. Phasellus nisl est, condimentum vitae faucibus in, sollicitudin vel metus. Nunc sit amet consequat risus. Curabitur ac elit leo. In eleifend dui tellus, in scelerisque elit porttitor et. Integer eu massa lacinia, lacinia nulla non.</p>
  </div>
</section>

<section class="abs gallery">
  <h3>Gallery</h3>
  <div class="shot" style="left:81px;background:linear-gradient(#6b6358,#b8b4ae 40%,#5a6a8a)" role="img" aria-label="Group photo of the dental mission team in Guatemala"></div>
  <div class="shot" style="left:226px;background:linear-gradient(#9a7a60,#c8b8a8 45%,#6a7080)" role="img" aria-label="Hall set up as a temporary dental clinic"></div>
  <div class="shot" style="left:372px;background:linear-gradient(#9ab0c0,#c09080 45%,#504a48)" role="img" aria-label="Street scene in a Guatemalan town"></div>
  <div class="shot" style="left:518px;background:linear-gradient(#a8a8a0,#6a6a70 50%,#3a3a40)" role="img" aria-label="Dentist treating a child patient"></div>
  <div class="dots"><i class="on"></i><i></i><i></i><i></i></div>
</section>

<div class="abs map" role="img" aria-label="Location map"></div>
<section class="abs form-area">
  <h3>Contact Us</h3>
  <div class="field" style="left:31px;top:42px">First Name</div>
  <div class="field" style="left:148px;top:42px">Last Name</div>
  <div class="field" style="left:31px;top:71px">Phone</div>
  <div class="field" style="left:148px;top:71px">Email</div>
  <div class="field" style="left:31px;top:101px">City</div>
  <div class="submit">SUBMIT</div>
</section>

<footer class="abs footer">
  <div class="f-row">
    <span style="width:216px"><svg width="6" height="8" viewBox="0 0 10 12"><path d="M5 0a4 4 0 0 0-4 4c0 3 4 8 4 8s4-5 4-8a4 4 0 0 0-4-4z" fill="#ddd"/></svg>Unit 4, 52 Fernway Boulevard, Wattlebrook, WA 6099</span>
    <span style="width:115px"><svg width="7" height="7" viewBox="0 0 10 10"><path d="M2 0l2 2.5-1 1.2c.6 1.3 1.7 2.4 3 3l1.2-1L10 8 8.5 10C4 9.5.5 6 0 1.5z" fill="#ddd"/></svg>Call Now: 08 5550 2718</span>
    <span><svg width="9" height="7" viewBox="0 0 12 9"><rect width="12" height="9" fill="#ddd"/><path d="M0 0l6 5 6-5" stroke="#3a3a3a" fill="none"/></svg>Email: &nbsp;info@harbourlightdental.com</span>
    <div class="social"><i></i><i></i><i></i><i></i></div>
  </div>
  <div class="f-rule"></div>
  <div class="f-links">Home &nbsp;| &nbsp;Meet the Team &nbsp;| &nbsp;Dental Treatments/Walk-in Treatments &nbsp;| &nbsp;Dental Advice &nbsp;| &nbsp;Contact us</div>
  <div class="copy">Copyright © 2016 &nbsp;The Harbourlight Dental centre. &nbsp;All rights reserved.</div>
  <div class="booking">Appointment Booking <b><i></i>clinic tidal</b></div>
</footer>
</body>
</html>
```